Vorn upkeep KT Solar Venture

Solar power system install
Services and maintenance
wiring, Rewinding and Renovation
Switch Board Upgrade
Power and lighting point
t doesn’t matter how much you spend on quality parts, your solar system will let you down if your design and installation are sub-par. Have your solar system tailored and installed by our Master Electrician and Bright Grid Guild Accredited team.

Target Market(s)

sales and installed

Industry/Entity Type

Solar install and retailer

Contact Information for Business Card

Name , Email, Phone Number ,Business address,

Font styles to use
Serif

Colors
0054AA
0677BA
7BADD7
CADEEF
E8F1F8

Requirements
Must have
• clear and bright
Nice to have
• new design
Should not have
• unclear pictures

```html
<!DOCTYPE html>
<html lang="en">
<head>
<meta charset="utf-8">
<title>Vorn Upkeep – Business Cards</title>
<link href="https://fonts.googleapis.com/css2?family=Roboto:wght@400;500;700;900&display=swap" rel="stylesheet">
<style>
  :root{
    --backdrop:#2b2b2b;
    --card:#f1f2f2;
    --card-edge:#e3e4e5;
    --brand-blue:#0054AA;
    --mid-blue:#0677BA;
    --sky:#7BADD7;
    --pale:#E8F1F8;
    --leaf:#3f9b35;
    --lime:#8cc63f;
    --sun:#f2b321;
    --ink:#1e1e1e;
    --muted-line:#cfd3d6;
  }
  *{box-sizing:border-box;margin:0;padding:0}
  html,body{width:1200px;height:1138px;overflow:hidden}
  body{background:var(--backdrop);font-family:'Roboto',sans-serif;position:relative}

  .card{position:absolute;width:623px;height:376px;border-radius:16px;overflow:hidden;
        background:linear-gradient(180deg,#f6f7f7,var(--card-edge))}
  .card--front{left:274px;top:186px}
  .card--back{left:275px;top:607px;width:620px;height:375px}

  /* brand lockup */
  .brand{position:absolute;display:flex;align-items:center;gap:16px}
  .brand__dot{width:86px;height:86px;border-radius:50%;background:var(--sun);flex:none}
  .brand__name{font-family:'Roboto',sans-serif;font-weight:900;color:var(--brand-blue);
               text-transform:uppercase;line-height:1.05;letter-spacing:.5px}
  .card--front .brand{left:110px;top:76px}
  .card--front .brand__name{font-size:32px}

  .services{position:absolute;left:0;top:238px;width:100%;height:75px;
            background:linear-gradient(90deg,#62a63a 0%,#3d9a6a 40%,var(--mid-blue) 75%,#0a6fb3 100%);
            color:#eef6ee;font-size:16.5px;text-align:center;display:flex;flex-direction:column;
            justify-content:center;gap:5px;font-weight:400}
  .services span.sep{margin:0 8px}

  .web-line{position:absolute;left:0;top:332px;width:100%;display:flex;align-items:center;justify-content:center;gap:30px}
  .web-line__rule{width:78px;height:2px}
  .web-line__rule--blue{background:linear-gradient(90deg,transparent,var(--mid-blue))}
  .web-line__rule--green{background:linear-gradient(90deg,var(--leaf),transparent)}
  .web-line__url{font-size:16px;color:var(--ink)}

  /* back */
  .back-panel{position:absolute;inset:0}
  .person{position:absolute;left:43px;top:68px;color:#fff}
  .person__name{font-size:26px;font-weight:700;color:var(--lime)}
  .person__role{font-size:16px;margin-top:3px;color:#eaf2fa}
  .address{position:absolute;left:43px;top:180px;font-size:16px;line-height:24px;color:#eaf2fa}
  .contacts{position:absolute;left:43px;top:234px;list-style:none;color:#eaf2fa;font-size:16px}
  .contacts li{display:flex;align-items:center;height:24px}
  .contacts svg{width:14px;height:14px;margin-right:17px;fill:var(--lime)}
  .card--back .brand{left:380px;top:110px;flex-direction:column;gap:14px;align-items:center}
  .card--back .brand__dot{width:78px;height:78px}
  .card--back .brand__name{font-size:27px;text-align:center}
</style>
</head>
<body>

<section class="card card--front">
  <div class="brand">
    <div class="brand__dot"></div>
    <div class="brand__name">Vorn Upkeep<br>Solar Venture</div>
  </div>
  <div class="services">
    <div>Solar Power System Install<span class="sep">|</span>Wiring, Rewinding &amp; Renovation</div>
    <div>Services &amp; Maintenance<span class="sep">|</span>Switch Board Upgrade<span class="sep">|</span>Power &amp; Lighting Point</div>
  </div>
  <div class="web-line">
    <span class="web-line__rule web-line__rule--blue"></span>
    <span class="web-line__url">www.ktsolarventure.com</span>
    <span class="web-line__rule web-line__rule--green"></span>
  </div>
</section>

<section class="card card--back">
  <svg class="back-panel" width="620" height="375" viewBox="0 0 620 375">
    <defs>
      <linearGradient id="panelBlue" x1="0" y1="0" x2="0" y2="1">
        <stop offset="0" stop-color="#0b4f97"/>
        <stop offset="1" stop-color="#0a78c4"/>
      </linearGradient>
    </defs>
    <path d="M0 0 H386 Q300 110 316 200 Q326 290 392 375 H0 Z" fill="var(--leaf)"/>
    <path d="M0 0 H381 Q295 110 310 200 Q320 290 384 375 H0 Z" fill="url(#panelBlue)"/>
  </svg>

  <div class="person">
    <div class="person__name">Dana Reyes Marlow</div>
    <div class="person__role">Managing Director</div>
  </div>
  <div class="address">58 Ridgeline Rd., Fernvale,<br>Lakeside, US 40219</div>
  <ul class="contacts">
    <li><svg viewBox="0 0 24 24"><path d="M6.6 10.8a15 15 0 0 0 6.6 6.6l2.2-2.2a1 1 0 0 1 1-.25 11.4 11.4 0 0 0 3.6.57 1 1 0 0 1 1 1V20a1 1 0 0 1-1 1A17 17 0 0 1 3 4a1 1 0 0 1 1-1h3.5a1 1 0 0 1 1 1c0 1.25.2 2.45.57 3.57a1 1 0 0 1-.25 1z"/></svg>555-014-2278</li>
    <li><svg viewBox="0 0 24 24"><path d="M2 5h20v14H2z M2 5l10 8 10-8" /></svg>dana@ktsolarventure.com</li>
    <li><svg viewBox="0 0 24 24"><circle cx="12" cy="12" r="10"/></svg>www.ktsolarventure.com</li>
  </ul>

  <div class="brand">
    <div class="brand__dot"></div>
    <div class="brand__name">Vorn Upkeep<br>Solar Venture</div>
  </div>
</section>

</body>
</html>
```